KVT Web Design Project

I would like a simple and elegant design for my international business consulting practice web site. I already have new KVT Logo and will have brochure-colors are blue, green and black

Practice areas:
I offer consulting services specializing in developing Internet-based anti-counterfeiting and anti-fraud programs, test purchases and investigations.

I offer Cyber Security, Data Protection and Compliance services

I also offer International Due Diligence Investigations and Country and Travel Risk Assessments

General Background Investigations

Physical Security Services

About me section listing my Bio

I have a set of key associates that I work with around the world and will want to list their CVs or Bios under "KVT

Associates"Banner with nice photo but not too cluttered

Ability to Upload documents and articles

Contact us section
Updates

I have uploaded my new logo-please advise if you didn't get it or it is not in the correct file format.

Thank you

Dominic

Hello Everyone,

Thank you for your submissions and ideas. I'm not sure about design only vs code. I understand that some of you do not do code-if not then please just provide design.

More about my business: see below link on Veridian Search docs to my brochure-this should help but don't use that phone number-see below.

https://files.quillbin.example/view?id=7Qx2Lm9Pz4Rt8Kw3Hn6Vb1Jc5Fd0Sg

 

Here are some details.

Contacts:

Dominic R. Torvello, CPP

President

Torvello and Associates, LLC

P.O. Box 47129

Gaithersburg, MD 20914

USA

web address:www.Torvelloandassociates.example (currently not working)

email:dom @torvelloand associates.example

Tel: 202-555-0173

I hope this is helpful. Dom

Reason: Sorry but during holiday period, have not had as much time to devote to this project. Thanks for your submissions.

Per my previous guidance, please keep designs simple and elegant and free from traditional security images with locks and chains-I prefer one or at most, two photos. Two colors- blue and green in addition to black for print. I want to present professional, corporate and international image. Thank you for your ideas nad submissions.

Dom

Target Market(s)

Law firms, large multi-national corporations, Security Industry

Industry/Entity Type

Business

Requirements
Must have
• Must have sections: (will provide text)

About KVT (will provide text)

Practice areas

Associates (will provide text)

Contact us

(it must also have ability to upload files and articles)
Should not have
• Old style fonts and symbols such as security badges, scales of justice, etc. I want a sleek and modern design.

```html
<!DOCTYPE html>
<html lang="en">
<head>
<meta charset="utf-8">
<title>Torvello &amp; Associates, LLC</title>
<link rel="stylesheet" href="https://fonts.googleapis.com/css2?family=Source+Sans+3:wght@400;600&family=Questrial&display=swap">
<style>
:root{
  --bg-top:#0a4fa0;
  --bg-bottom:#1a9ad8;
  --page:#ffffff;
  --header-top:#ffffff;
  --header-bottom:#efefef;
  --green:#5a9a1a;
  --green-dark:#3f7a10;
  --green-light:#72b428;
  --heading-green:#5c9e12;
  --blue:#1f5f9e;
  --blue-title:#1a5aa0;
  --blue-link:#3a9ad6;
  --banner-top:#3a9cdc;
  --banner-bottom:#2580c4;
  --text:#333333;
  --field-border:#b9c0c6;
}
*{box-sizing:border-box;margin:0;padding:0}
html,body{width:1052px;height:1200px;overflow:hidden}
body{background:linear-gradient(var(--bg-top),var(--bg-bottom));font-family:"Questrial",sans-serif;color:var(--text);position:relative}
h2,h3{font-weight:400}
.page{position:absolute;left:142px;top:19px;width:771px;height:1156px;background:var(--page);box-shadow:0 0 12px rgba(0,0,0,.35)}
.abs{position:absolute}
.site-header{left:0;top:0;width:771px;height:96px;background:linear-gradient(var(--header-top),var(--header-bottom))}
.brand{left:30px;top:26px;font-family:"Source Sans 3",sans-serif;color:var(--blue)}
.brand-name{font-size:20px;color:#1b2f4a;display:flex;align-items:center;gap:8px}
.brand-mark{font-size:22px;color:var(--blue);padding-right:8px;border-right:1px solid #556}
.brand-tag{font-size:11.5px;letter-spacing:1.6px;margin-top:2px;color:var(--blue)}
.call{right:54px;top:28px;font-family:"Source Sans 3",sans-serif;font-size:13px;color:var(--green)}
.call b{color:var(--blue-title);font-weight:400}
.search{right:54px;top:48px;width:122px;height:16px;border-radius:8px;background:#2c8bd0;color:#fff;font-size:9px;padding:2px 10px;font-family:"Source Sans 3",sans-serif}
.search svg{position:absolute;right:7px;top:3px}
.main-nav{left:0;top:96px;width:771px;height:37px;background:linear-gradient(var(--green-light),var(--green));display:flex;padding-left:142px}
.main-nav a{font-family:"Source Sans 3",sans-serif;color:#fff;font-size:15px;text-decoration:none;padding:0 7px;line-height:37px}
.main-nav a.current{background:var(--green-dark);border-radius:4px 4px 0 0;margin-top:-6px;line-height:49px;padding:0 11px;position:relative}
.banner{left:11px;top:133px;width:748px;height:229px;border-radius:0 0 8px 8px;background:linear-gradient(var(--banner-top),var(--banner-bottom))}
.service{left:15px;width:299px;height:35px;background:linear-gradient(#2a7dbd,#1c66a6);color:#fff;font-family:"Source Sans 3",sans-serif;font-size:12px;text-align:center;line-height:35px;box-shadow:0 1px 2px rgba(0,0,0,.25)}
.banner-photo{left:333px;top:12px;width:403px;height:194px;border:4px solid #fff;border-radius:4px;background:linear-gradient(180deg,#7fe0f4 0%,#2fa9d8 55%,#0e3f72 100%)}
.dots{left:657px;top:179px;display:flex;gap:6px}
.dots span{width:10px;height:10px;border-radius:50%;background:#fff}
.dots span.on{background:var(--green-light)}
.h{font-family:"Source Sans 3",sans-serif;color:var(--heading-green);font-size:14.5px;text-transform:uppercase;font-weight:400}
.copy{font-size:11.3px;line-height:15px;text-indent:14px;letter-spacing:.25px}
.field{width:116px;height:18px;border:1px solid var(--field-border);border-radius:5px;font-size:6px;padding:5px 6px;color:#666;left:564px}
.msg{left:564px;top:495px;width:167px;height:100px;border:1px solid var(--field-border);border-radius:5px}
.btn{height:19px;border:1px solid #aaa;border-radius:9px;background:linear-gradient(#fff,#dcdcdc);font-family:"Source Sans 3",sans-serif;font-size:11px;line-height:17px;text-align:center;color:#444}
.col-title{font-family:"Source Sans 3",sans-serif;color:var(--blue-title);font-size:14.5px;line-height:18px;font-weight:400}
.item-title{font-family:"Source Sans 3",sans-serif;color:var(--blue-title);font-size:14.5px}
.item-sub{font-size:11px;color:var(--blue-link);margin-top:4px}
.news p{font-size:11.3px;line-height:14px}
.read{font-family:"Source Sans 3",sans-serif;color:var(--blue-title);font-size:13px;font-weight:600;text-align:right;margin-top:-4px;width:218px}
.site-footer{left:0;top:1125px;width:771px;height:31px;background:linear-gradient(var(--green-light),var(--green));color:#fff;font-family:"Source Sans 3",sans-serif;font-size:11px;line-height:31px;padding-left:27px}
.site-footer .links{margin-left:24px}
.social{right:24px;top:0;font-size:16px;font-weight:600;display:flex;gap:8px}
</style>
</head>
<body>
<div class="page">
  <header class="site-header abs">
    <div class="brand abs">
      <div class="brand-name"><span class="brand-mark">KVT</span>Torvello &amp; Associates, LLC</div>
      <div class="brand-tag">Intellectual Property and Cyber Security</div>
    </div>
    <div class="call abs">Call us <b>202-555-0173</b></div>
    <div class="search abs">Search
      <svg width="10" height="10" viewBox="0 0 10 10"><circle cx="6" cy="4" r="3" fill="none" stroke="#fff" stroke-width="1.3"/><line x1="4" y1="6" x2="1" y2="9" stroke="#fff" stroke-width="1.5"/></svg>
    </div>
  </header>

  <nav class="main-nav abs">
    <a class="current" href="#">Home</a><a href="#">About us</a><a href="#">Practice Area</a><a href="#">Careers</a><a href="#">Media</a><a href="#">Contact us</a>
  </nav>

  <section class="banner abs">
    <div class="service abs" style="top:10px">Cyber Security and Data Protection</div>
    <div class="service abs" style="top:51px">Compliance services</div>
    <div class="service abs" style="top:94px">International Due Diligence Investigations</div>
    <div class="service abs" style="top:136px">Country and Travel Risk Assessments</div>
    <div class="service abs" style="top:179px">Physical Security Services</div>
    <svg class="abs" style="left:322px;top:146px" width="10" height="16" viewBox="0 0 10 16"><polygon points="10,0 0,8 10,16" fill="#8cc6ee"/></svg>
    <div class="banner-photo abs" role="img" aria-label="Photo: group of business people silhouetted in front of a glowing blue world map"></div>
    <div class="dots abs"><span class="on"></span><span></span><span></span><span></span></div>
  </section>

  <section class="abs" style="left:32px;top:387px;width:232px">
    <h2 class="h" style="margin-left:15px">What we do</h2>
    <p class="copy" style="margin-top:9px">Lorem ipsum dolor sit amet, consectetuer adipiscing elit, sed diam nonummy nibh euismod tincidunt ut laoreet dolore magna aliquam erat volutpat. Ut wisi enim ad minim veniam, quis nostrud exerci tation ullamcorper suscipit lobortis nisl ut aliquip ex ea commodo consequat. Duis autem vel eum iriure dolor in hendrerit in vulputate velit esse molestie consequat, vel illum dolore eu feugiat nulla facilisis at vero eros et accumsan et iusto odio dignissim qui blandit praesent luptatum zzril delenit augue duis dolore te feugait.</p>
  </section>

  <section class="abs" style="left:298px;top:385px;width:232px">
    <h2 class="h" style="margin-left:15px">Generic statement</h2>
    <p class="copy" style="margin-top:9px">Epsum factorial non deposit quid pro quo hic escorol. Olypian quarrels et gorilla congolium sic ad nauseum. Souvlaki ignitus carborundum e pluribus unum. Defacto lingo est igpay atinlay. Marquee selectus non provisio incongruous feline nolo contendre. Gratuitous octopus niacin, sodium glutimate. Quote meon an estimate et non interruptus stadium. Sic tempus fugit esperanto hiccup estrogen. Glorious baklava ex librus hup hey ad infinitum. Non sequitur condominium facile et geranium incognito.</p>
  </section>

  <h2 class="h abs" style="left:564px;top:388px">Contact us</h2>
  <div class="field abs" style="top:416px">FULL NAME</div>
  <div class="field abs" style="top:442px">EMAIL</div>
  <div class="field abs" style="top:468px">ADDRESS</div>
  <div class="msg abs"></div>
  <div class="btn abs" style="left:604px;top:604px;width:82px">Attach a File</div>
  <div class="btn abs" style="left:694px;top:604px;width:52px">Send</div>

  <h2 class="h abs" style="left:43px;top:632px">Practice area</h2>
  <section class="abs" style="left:43px;top:668px;width:158px">
    <h3 class="col-title" style="margin-left:3px">Cyber Security</h3>
    <p class="copy" style="margin-top:17px">Li Europan lingues es membres del sam familie. Lor separat existentie es un myth. Por scientie, musica, sport etc, li tot Europa usa li sam vocabularium. Li lingues differe solmen in li grammatica.</p>
  </section>
  <section class="abs" style="left:217px;top:662px;width:158px">
    <h3 class="col-title" style="margin-left:3px">International<br>Investigations</h3>
    <p class="copy" style="margin-top:5px">Li Europan lingues es membres del sam familie. Lor separat existentie es un myth. Por scientie, musica, sport etc, li tot Europa usa li sam vocabularium. Li lingues differe solmen in li grammatica.</p>
  </section>
  <section class="abs" style="left:390px;top:672px;width:158px">
    <h3 class="col-title">Travel risk Assessments</h3>
    <p class="copy" style="margin-top:10px">Li Europan lingues es membres del sam familie. Lor separat existentie es un myth. Por scientie, musica, sport etc, li tot Europa usa li sam vocabularium. Li lingues differe solmen in li grammatica.</p>
  </section>
  <section class="abs" style="left:563px;top:673px;width:158px">
    <h3 class="col-title" style="margin-left:3px">Physical Security</h3>
    <p class="copy" style="margin-top:10px">Li Europan lingues es membres del sam familie. Lor separat existentie es un myth. Por scientie, musica, sport etc, li tot Europa usa li sam vocabularium. Li lingues differe solmen in li grammatica.</p>
  </section>

  <section class="abs" style="left:45px;top:862px;width:220px">
    <h2 class="h">Latest articles</h2>
    <div style="margin-top:14px"><div class="item-title" style="margin-left:12px">Phisical Security</div><div class="item-sub" style="margin-left:3px">Lorem ipsum dolor sit amet</div></div>
    <div style="margin-top:10px"><div class="item-title" style="margin-left:14px">International Investigations</div><div class="item-sub" style="margin-left:3px">Lorem ipsum dolor sit amet</div></div>
    <div style="margin-top:10px"><div class="item-title" style="margin-left:11px">Travel risk Assessments</div><div class="item-sub" style="margin-left:2px">Lorem ipsum dolor sit amet</div></div>
    <div style="margin-top:10px"><div class="item-title" style="margin-left:13px">Cyber Security</div><div class="item-sub" style="margin-left:2px">Lorem ipsum dolor sit amet</div></div>
  </section>

  <section class="news abs" style="left:292px;top:862px;width:240px">
    <h2 class="h" style="margin-left:7px">Latest news</h2>
    <div class="item-title" style="margin:14px 0 4px 7px">Merry Christmas 22/12/2011</div>
    <p>Lorem ipsum dolor sit amet, consectetuer adipiscing elit, sed diam nonummy nibh euismod tincidunt ut...</p>
    <div class="read">Read More</div>
    <div class="item-title" style="margin:12px 0 4px 7px">Lorem ipsum&nbsp; 17/12/2011</div>
    <p>Lorem ipsum dolor sit amet, consectetuer adipiscing elit, sed diam nonummy nibh euismod tincidunt ut...</p>
    <div class="read">Read More</div>
  </section>

  <section class="news abs" style="left:566px;top:861px;width:170px">
    <h2 class="h" style="line-height:18px">Associations&nbsp; we<br>&nbsp;work with</h2>
    <div class="item-title" style="margin:11px 0 1px 3px">Northgate Hosting</div>
    <p style="margin-left:3px">Lorem ipsum dolor sit amet, consectetuer sed diam ...</p>
    <div class="item-title" style="margin:5px 0 1px 3px">Veridian Search</div>
    <p style="margin-left:3px">Lorem ipsum dolor sit amet, consectetuer sed diam ...</p>
  </section>

  <footer class="site-footer abs">
    © 2011 KVT <span class="links">Privacy Policy | Copyright | Site Map | Contact Us</span>
    <div class="social abs"><span>Friendsphere</span><span>Chirpline</span></div>
  </footer>
</div>
</body>
</html>
```